Velvet Riot Rising Line of Sparkling Wine & Spirits

Back info: Nora Beth Quill Owner 555-318-4402 1480 E. Harlow Ave, Bldg. 2, & 3, Fairbrook Or. 95871
Sparkling Wines & Collectibles www.velvetriotrising.com
Ok I have uploaded the winning design. The color that I am after is the Fushia, Raspberry, Red, Matte Satin Matalic Finish. With a 24 Karet Gold color Foil. The Bottle is on the top row and it's the 2nd Bottle in. That is the Color that I want. This is the style of font. Make sure that you put what we're advertising. Good Luck to you all. Warmest regards, Nora
21 & up UniSex
Sparkling Wine and Memorabilia
there listed up above.....

```html
<!DOCTYPE html>
<html lang="en">
<head>
<meta charset="utf-8">
<title>Velvet Riot Rising – Business Cards</title>
<link rel="stylesheet" href="https://fonts.googleapis.com/css2?family=Almendra:wght@700&family=Montserrat:wght@400;500;700&display=swap">
<style>
  :root {
    --backdrop: #c9c9c9;
    --fuchsia-light: #e0168f;
    --fuchsia-mid: #c9127a;
    --fuchsia-deep: #a00e50;
    --gold: #f2c21e;
    --ink: #2b2b2e;
    --card-w: 720px;
    --card-h: 411px;
  }
  * { box-sizing: border-box; margin: 0; padding: 0; }
  html, body { width: 1200px; height: 1015px; overflow: hidden; }
  body {
    background: var(--backdrop);
    font-family: "Montserrat", sans-serif;
    display: flex;
    flex-direction: column;
    align-items: center;
    justify-content: center;
    gap: 60px;
  }
  .card {
    position: relative;
    width: var(--card-w);
    height: var(--card-h);
    background: radial-gradient(ellipse 90% 70% at 50% 50%, var(--fuchsia-light) 0%, var(--fuchsia-mid) 55%, var(--fuchsia-deep) 100%);
    box-shadow: 0 6px 18px rgba(0,0,0,.35);
    color: var(--gold);
  }

  /* Front */
  .front .brand-name {
    position: absolute;
    top: 138px; left: 0; right: 0;
    text-align: center;
    font-weight: 700;
    font-size: 50px;
    line-height: 1;
    color: var(--ink);
  }
  .front .tagline {
    position: absolute;
    top: 250px; left: 0; right: 0;
    display: flex;
    align-items: center;
    justify-content: center;
    gap: 10px;
    font-weight: 500;
    font-size: 18px;
    letter-spacing: 1.5px;
    text-transform: uppercase;
  }
  .sparkles { width: 46px; height: 46px; flex: none; }

  /* Back */
  .back .brand-name {
    position: absolute;
    top: 62px; right: 50px;
    font-weight: 700;
    font-size: 40px;
    line-height: 1;
  }
  .back .owner {
    position: absolute;
    left: 50px; top: 172px;
  }
  .owner-name {
    font-family: "Almendra", serif;
    font-weight: 700;
    font-size: 34px;
    line-height: 1;
  }
  .owner-role { font-size: 17px; margin-top: 4px; }
  .divider {
    position: absolute;
    left: 50px; right: 50px; top: 248px;
    height: 1px;
    background: var(--gold);
  }
  .contacts {
    position: absolute;
    left: 50px; top: 270px;
    list-style: none;
    font-size: 18px;
    line-height: 1.55;
  }
  .contacts li { display: flex; align-items: center; gap: 12px; }
  .contacts svg { width: 18px; height: 18px; flex: none; }
  .back .address {
    position: absolute;
    right: 50px; top: 268px;
    text-align: right;
    font-style: normal;
    font-size: 17px;
    line-height: 1.35;
  }
</style>
</head>
<body>
  <section class="card front" aria-label="Card front">
    <h1 class="brand-name">Velvet Riot Rising</h1>
    <p class="tagline">
      <svg class="sparkles" viewBox="0 0 46 46" aria-hidden="true" fill="var(--gold)">
        <path d="M30 2 L31.5 9 L38 10.5 L31.5 12 L30 19 L28.5 12 L22 10.5 L28.5 9 Z"/>
        <path d="M18 12 L20 24 L36 25 L20 26 L18 42 L16 26 L2 25 L16 24 Z"/>
        <path d="M12 30 L13.5 36 L19 37 L13.5 38 L12 44 L10.5 38 L5 37 L10.5 36 Z"/>
      </svg>
      Sparkling Wines &amp; Collectibles
    </p>
  </section>

  <section class="card back" aria-label="Card back">
    <h2 class="brand-name">Velvet Riot Rising</h2>
    <div class="owner">
      <p class="owner-name">Nora Beth Quill</p>
      <p class="owner-role">Owner</p>
    </div>
    <div class="divider"></div>
    <ul class="contacts">
      <li>
        <svg viewBox="0 0 24 24" aria-hidden="true" fill="var(--gold)"><path d="M6.6 10.8a15 15 0 0 0 6.6 6.6l2.2-2.2a1 1 0 0 1 1-.25 11.4 11.4 0 0 0 3.6.57 1 1 0 0 1 1 1V20a1 1 0 0 1-1 1A17 17 0 0 1 3 4a1 1 0 0 1 1-1h3.5a1 1 0 0 1 1 1c0 1.25.2 2.45.57 3.6a1 1 0 0 1-.25 1Z"/></svg>
        555-318-4402
      </li>
      <li>
        <svg viewBox="0 0 24 24" aria-hidden="true" fill="var(--gold)"><path d="M2 5h20v14H2z M4 7v.5l8 5 8-5V7l-8 5z" fill-rule="evenodd"/></svg>
        hello@velvetriotrising.com
      </li>
      <li>
        <svg viewBox="0 0 24 24" aria-hidden="true" fill="none" stroke="var(--gold)" stroke-width="2"><circle cx="12" cy="12" r="9"/><path d="M3 12h18M12 3c3 3 3 15 0 18M12 3c-3 3-3 15 0 18"/></svg>
        www.velvetriotrising.com
      </li>
    </ul>
    <address class="address">
      1480 E. Harlow Ave<br>Bldg. 2, &amp; 3<br>Fairbrook Or. 95871
    </address>
  </section>
</body>
</html>
```